Business Card Design

We are a commercial real estate brokerage in San Francisco, leasing office buildings downtown.
I would like a clean, elegant look. Simple but powerful .

Industry/Entity Type

Business

Contact Information for Business Card

Derek Holloway
lic# 07258143
415.555.0172
derek@velt-commercial.example
velt-commercial.example

```html
<!DOCTYPE html>
<html lang="en">
<head>
<meta charset="utf-8">
<title>Velt Commercial – Business Card</title>
<link href="https://fonts.googleapis.com/css2?family=Source+Sans+3:wght@400;600&display=swap" rel="stylesheet">
<style>
  :root {
    --page-bg: #e9e9e9;
    --card-bg: #0f1013;
    --card-bg-edge: #131419;
    --accent: #8796b3;
    --text: #f2f3f5;
    --divider: #2a2c33;
    --art-top: #5a5d66;
    --art-bottom: #26282e;
  }
  * { margin: 0; padding: 0; box-sizing: border-box; }
  html, body { width: 1200px; height: 900px; overflow: hidden; }
  body {
    background: var(--page-bg);
    font-family: "Source Sans 3", "Myriad Pro", sans-serif;
    position: relative;
  }
  .card {
    position: absolute;
    top: 271px;
    width: 457px;
    height: 281px;
    border-radius: 14px;
    background: radial-gradient(ellipse at 50% 45%, var(--card-bg-edge), var(--card-bg) 70%);
    box-shadow: 0 1px 3px rgba(0,0,0,0.25);
  }
  .card--front { left: 137px; }
  .card--back { left: 626px; }

  .skyline-art {
    position: absolute;
    background: linear-gradient(180deg, var(--art-top), var(--art-bottom));
    border-radius: 2px;
  }
  .card--front .skyline-art { left: 30px; top: 86px; width: 166px; height: 110px; }
  .card--back .skyline-art { left: 86px; top: 108px; width: 100px; height: 66px; }

  .divider {
    position: absolute;
    width: 1px;
    background: var(--divider);
  }
  .card--front .divider { left: 218px; top: 68px; height: 150px; }
  .card--back .divider { left: 197px; top: 97px; height: 87px; }

  .contact {
    position: absolute;
    left: 236px;
    top: 78px;
  }
  .contact__name {
    color: var(--accent);
    font-size: 17px;
    font-weight: 600;
    letter-spacing: 0.2px;
    margin-bottom: 15px;
  }
  .contact__list { list-style: none; }
  .contact__item {
    display: flex;
    align-items: center;
    gap: 7px;
    color: var(--text);
    font-size: 13px;
    line-height: 19px;
    margin-left: 1px;
  }
  .contact__icon { width: 9px; height: 9px; fill: var(--accent); stroke: var(--accent); flex: none; }
  .contact__licence {
    margin-top: 15px;
    font-size: 13px;
    font-weight: 600;
    color: var(--text);
  }
  .contact__licence-label { color: var(--accent); }

  .brand-name {
    position: absolute;
    left: 210px;
    top: 118px;
    color: var(--accent);
    font-size: 33px;
    font-weight: 600;
    line-height: 1;
    white-space: nowrap;
  }
</style>
</head>
<body>
  <section class="card card--front">
    <div class="skyline-art" role="img" aria-label="Illustration of a downtown office skyline in greys"></div>
    <div class="divider"></div>
    <div class="contact">
      <p class="contact__name">Derek Holloway</p>
      <ul class="contact__list">
        <li class="contact__item">
          <svg class="contact__icon" viewBox="0 0 10 10" aria-hidden="true"><path stroke="none" d="M2 0.5 L3.6 2.6 L2.7 3.6 C3.3 5 4.8 6.6 6.3 7.2 L7.3 6.3 L9.5 7.9 L8.4 9.5 C4.5 9.2 0.8 5.5 0.5 1.6 Z"/></svg>
          415.555.0172
        </li>
        <li class="contact__item">
          <svg class="contact__icon" viewBox="0 0 10 10" aria-hidden="true"><rect x="0.5" y="2" width="9" height="6.5" stroke="none"/><path d="M0.8 2.3 L5 5.6 L9.2 2.3" fill="none" stroke="#0f1013" stroke-width="1"/></svg>
          derek@velt-commercial.example
        </li>
        <li class="contact__item">
          <svg class="contact__icon" viewBox="0 0 10 10" aria-hidden="true" fill="none"><path d="M4.2 6.8 L2.8 8.2 A1.6 1.6 0 0 1 0.8 6.2 L2.6 4.4 A1.6 1.6 0 0 1 4.8 4.6 M5.8 3.2 L7.2 1.8 A1.6 1.6 0 0 1 9.2 3.8 L7.4 5.6 A1.6 1.6 0 0 1 5.2 5.4" fill="none" stroke-width="1.1"/></svg>
          velt-commercial.example
        </li>
      </ul>
      <p class="contact__licence"><span class="contact__licence-label">Lic#</span> 07258143</p>
    </div>
  </section>

  <section class="card card--back">
    <div class="skyline-art" role="img" aria-label="Illustration of a downtown office skyline in greys"></div>
    <div class="divider"></div>
    <p class="brand-name">Velt Commercial</p>
  </section>
</body>
</html>
```